Dorla's Cleaners new delivery postcard

We need to advertise for our new pick up and delivery dry cleaning/laundry service.
Mens Business Shirts $2.00
Pants $4.50
Skirts $5.00
Dry Clean Shirt/Blouse $5.00
Dress $9.00
2 Piece Suits $9.00
Updates
We would like to use a 5x7 size postcard, printed on both sides. We would like to add a discount to the card for 25% off of their first order, with the flyer.
We are a famly run dry cleaners. My name is Rosalind Tupper and my cell # is 614-302-7781. We are trying to expand our business to include free pick and delivery.
If possible can you use the logo I sent some where on the postcard? The phone # for the store is 614-295-3064.
Reason: Still need to get partners approval.

```html
<!DOCTYPE html>
<html lang="en">
<head>
<meta charset="utf-8">
<title>Dorla's Cleaners – Delivery Postcard</title>
<link href="https://fonts.googleapis.com/css2?family=Montserrat:wght@600;700;800&family=Questrial&display=swap" rel="stylesheet">
<style>
  :root {
    --orange: #f47b20;
    --blue: #1a9fd9;
    --green: #7ab52e;
    --navy: #1f3f73;
    --phone-blue: #2a5aa8;
    --paper: #ffffff;
    --paper-edge: #e4e6e8;
    --water-light: #cfe9ef;
    --water-mid: #4a9fb3;
    --water-deep: #0e4a63;
    --panel: rgba(255, 255, 255, 0.78);
  }
  html, body {
    margin: 0;
    padding: 0;
    overflow: hidden;
    background: #f2f2f2;
  }
  .postcard {
    position: relative;
    width: 1200px;
    height: 856px;
    overflow: hidden;
    background: linear-gradient(180deg, var(--paper-edge) 0%, var(--paper) 12%, var(--paper) 86%, var(--paper-edge) 100%);
    font-family: "Questrial", "Helvetica Neue", Arial, sans-serif;
  }
  .brand {
    position: absolute;
    left: 36px;
    top: 30px;
    display: flex;
    align-items: center;
    gap: 16px;
  }
  .brand-dot {
    width: 70px;
    height: 70px;
    border-radius: 50%;
    background: var(--blue);
  }
  .brand-name {
    font-family: "Montserrat", Arial, sans-serif;
    font-weight: 600;
    font-size: 54px;
    color: var(--orange);
    letter-spacing: -0.5px;
  }
  .delivery-tag {
    position: absolute;
    right: 42px;
    top: 46px;
    margin: 0;
    font-family: "Montserrat", Arial, sans-serif;
    font-weight: 700;
    font-size: 32px;
    color: var(--green);
    text-align: right;
    line-height: 1;
  }
  .photo-band {
    position: absolute;
    left: 0;
    top: 0;
    width: 1200px;
    height: 856px;
  }
  .offer {
    position: absolute;
    left: 184px;
    top: 384px;
    margin: 0;
    font-family: "Montserrat", Arial, sans-serif;
    font-weight: 700;
    line-height: 1;
  }
  .offer-amount {
    display: block;
    font-size: 128px;
    font-weight: 800;
    color: var(--orange);
    letter-spacing: -3px;
  }
  .offer-label {
    display: block;
    font-size: 70px;
    color: var(--blue);
    margin-top: -4px;
    letter-spacing: -1px;
  }
  .offer-condition {
    display: block;
    font-size: 44px;
    color: var(--green);
    margin-top: 2px;
  }
  .services {
    position: absolute;
    left: 750px;
    top: 312px;
    width: 398px;
    height: 404px;
    background: var(--panel);
    border-radius: 14px;
    box-sizing: border-box;
    padding: 16px 0 0 32px;
  }
  .services-kicker {
    font-family: "Montserrat", Arial, sans-serif;
    font-weight: 600;
    font-size: 33px;
    color: var(--orange);
    line-height: 1.1;
  }
  .services-title {
    font-family: "Montserrat", Arial, sans-serif;
    font-weight: 700;
    font-size: 56px;
    color: var(--blue);
    line-height: 1;
    margin: 0 0 10px;
  }
  .services-list {
    list-style: none;
    margin: 0;
    padding: 0;
  }
  .services-list li {
    font-size: 36px;
    color: var(--navy);
    line-height: 53px;
  }
  .services-list li::before {
    content: "•";
    margin: 0 10px 0 2px;
  }
  .contact {
    position: absolute;
    left: 56px;
    top: 762px;
    display: flex;
    align-items: center;
    gap: 10px;
    font-size: 50px;
    color: var(--phone-blue);
    letter-spacing: -0.5px;
  }
  .contact svg { width: 30px; height: 34px; }
  .price-list {
    position: absolute;
    left: 806px;
    top: 756px;
    width: 356px;
    margin: 0;
    padding: 0;
    list-style: none;
    display: grid;
    grid-template-columns: 1fr 1fr;
    column-gap: 22px;
    font-size: 19px;
    line-height: 27px;
    color: var(--navy);
  }
  .price-list li {
    display: flex;
    justify-content: space-between;
    white-space: nowrap;
  }
  .price-list .price {
    color: var(--orange);
    margin-left: 6px;
  }
</style>
</head>
<body>
  <main class="postcard">
    <div class="brand">
      <span class="brand-dot"></span>
      <span class="brand-name">Dorla's Cleaners</span>
    </div>

    <p class="delivery-tag">Free pick-up &amp; delivery</p>

    <svg class="photo-band" viewBox="0 0 1200 856" role="img" aria-label="Underwater photograph of rising air bubbles in clear blue-green water">
      <defs>
        <radialGradient id="water" cx="0.18" cy="0.45" r="0.95">
          <stop offset="0" stop-color="#eef8fa"/>
          <stop offset="0.18" stop-color="var(--water-light)"/>
          <stop offset="0.5" stop-color="var(--water-mid)"/>
          <stop offset="1" stop-color="var(--water-deep)"/>
        </radialGradient>
      </defs>
      <path d="M0 146 Q600 114 1200 124 L1200 730 Q600 696 0 702 Z" fill="url(#water)"/>
    </svg>

    <h1 class="offer">
      <span class="offer-amount">25%</span>
      <span class="offer-label">discount</span>
      <span class="offer-condition">on first order</span>
    </h1>

    <section class="services">
      <div class="services-kicker">additional</div>
      <h2 class="services-title">Services</h2>
      <ul class="services-list">
        <li>Dry cleaning</li>
        <li>Shirt laundry</li>
        <li>Alterations</li>
        <li>Wedding dresses</li>
        <li>Storage</li>
      </ul>
    </section>

    <div class="contact">
      <svg viewBox="0 0 24 28" aria-hidden="true">
        <path d="M6 2 L10 2 L11 8 L8 10 Q10 16 14 19 L17 16 L22 18 L22 23 Q20 27 15 25 Q5 20 3 9 Q2 3 6 2 Z" fill="var(--green)"/>
      </svg>
      <span>614-302-7781 / &nbsp;614-295-3064</span>
    </div>

    <ul class="price-list" aria-label="Price list">
      <li><span>Men's Shirts</span><span class="price">$2.00</span></li>
      <li><span>Pants</span><span class="price">$4.50</span></li>
      <li><span>Skirts</span><span class="price">$5.00</span></li>
      <li><span>Shirt/Blouse</span><span class="price">$5.00</span></li>
      <li><span>Dress</span><span class="price">$9.00</span></li>
      <li><span>2-Pc Suit</span><span class="price">$9.00</span></li>
    </ul>
  </main>
</body>
</html>
```